Plakat für Hausverwaltung
Zielgruppe
Hausverwaltung
(Verwaltung von Wohn- und Gewerbeimmobilien)
Aufgabenstellung
Es soll ein Werbeplakat werden, Die Inhalte der Dienstleistung und die Firmenfarben kann der Webseite entnommen werden.
Ein guter Werbespruch und ansprechendes Desing ohne viel Schrift.

```html
<!DOCTYPE html>
<html lang="de">
<head>
<meta charset="utf-8">
<title>LWR Hausverwaltung – Banner</title>
<link rel="stylesheet" href="https://fonts.googleapis.com/css2?family=Barlow+Condensed:wght@400&family=Montserrat:wght@400;500;600&family=Tinos&family=Roboto:wght@400&display=swap">
<style>
  :root {
    --page: #bfc0c2;
    --light-top: #dedbd6;
    --light-bottom: #c8c3bc;
    --photo-a: #cfcac4;
    --photo-b: #a9a29a;
    --ink: #4a3f35;
    --dark: #232020;
    --dark-2: #2b2726;
    --tan: #a8957c;
    --tan-dark: #8a7760;
    --text-light: #eeeae4;
    --text-muted: #b9ab97;
  }
  * { box-sizing: border-box; margin: 0; padding: 0; }
  html, body { width: 1200px; height: 900px; overflow: hidden; }
  body { background: var(--page); position: relative; font-family: "Montserrat", sans-serif; }

  .banner {
    position: absolute; left: 20px; top: 158px;
    width: 1160px; height: 585px;
    background: linear-gradient(160deg, var(--light-top), var(--light-bottom));
    overflow: hidden;
  }
  .team-photo {
    position: absolute; left: 575px; top: 0; width: 585px; height: 320px;
    background: linear-gradient(180deg, var(--photo-a), var(--photo-b));
  }
  .dark-field { position: absolute; inset: 0; }

  .brand { position: absolute; left: 125px; top: 30px; display: flex; align-items: center; gap: 10px; }
  .brand-name { font-family: "Montserrat", sans-serif; font-weight: 500; font-size: 34px; letter-spacing: 10px; color: var(--ink); }
  .brand-mark { width: 30px; height: 30px; border: 2px solid var(--ink); }
  .brand-sub { position: absolute; left: 29px; top: 73px; font-family: "Tinos", serif; font-size: 19px; color: #222; }

  .headline {
    position: absolute; left: 29px; top: 113px;
    font-family: "Barlow Condensed", sans-serif; font-weight: 400;
    font-size: 50px; line-height: 57px; color: var(--ink);
  }

  .features { position: absolute; left: 19px; top: 256px; display: flex; }
  .feature { display: flex; align-items: center; gap: 8px; font-family: "Roboto", sans-serif; font-size: 9px; line-height: 11px; color: var(--text-muted); }
  .feature svg { width: 24px; height: 24px; stroke: var(--tan-dark); fill: none; stroke-width: 1.3; }
  .feature:nth-child(1) { width: 100px; }
  .feature:nth-child(2) { width: 121px; }
  .feature:nth-child(3) { width: 139px; }
  .features-rule { position: absolute; left: 0; top: 300px; width: 518px; height: 1px; background: var(--tan-dark); }

  .offers-label {
    position: absolute; left: 0; top: 301px; width: 250px; height: 27px;
    background: var(--tan);
    clip-path: polygon(0 0, 100% 0, 93% 100%, 0 100%);
    font-size: 19px; font-weight: 500; color: var(--dark); padding: 1px 0 0 25px;
  }

  .offer { position: absolute; top: 343px; color: var(--text-light); }
  .offer-title { display: flex; align-items: center; gap: 9px; font-size: 17px; font-weight: 600; margin-left: -28px; }
  .offer-num { width: 20px; height: 20px; border-radius: 50%; background: var(--tan-dark); color: var(--dark); font-size: 10px; display: flex; align-items: center; justify-content: center; font-weight: 500; }
  .offer-list { list-style: none; margin-top: 8px; font-size: 11.4px; line-height: 14.3px; font-weight: 400; }
  .offer-list li::before { content: "▪ "; font-size: 8px; vertical-align: 1px; }
  .offer--special { left: 53px; }
  .offer--owner { left: 542px; }
  .offer--rent { left: 917px; }

  .contact { position: absolute; left: 976px; top: 462px; font-size: 11px; line-height: 14px; color: var(--text-muted); }
  .contact-row { display: flex; gap: 8px; align-items: flex-start; margin-bottom: 7px; }
  .contact-row svg { width: 14px; height: 14px; stroke: var(--text-muted); fill: none; stroke-width: 1.2; flex: none; }

  .web {
    position: absolute; left: 933px; top: 540px; width: 227px; height: 23px;
    background: var(--tan);
    clip-path: polygon(6% 0, 100% 0, 100% 100%, 0 100%);
    font-size: 12px; color: var(--dark); text-align: center; padding-top: 4px; padding-left: 12px;
  }
  .web strong { font-weight: 600; }
</style>
</head>
<body>
<div class="banner">
  <div class="team-photo" role="img" aria-label="Foto: drei Teammitglieder in Businesskleidung vor einem Aktenregal"></div>

  <svg class="dark-field" viewBox="0 0 1160 585" aria-hidden="true">
    <polygon points="0,249 518,249 559,319 1160,319 1160,585 0,585" fill="var(--dark)"/>
  </svg>

  <div class="brand">
    <span class="brand-name">LWR</span>
    <span class="brand-mark"></span>
  </div>
  <div class="brand-sub">Haus- und Grundstücksverwaltungs GmbH</div>

  <h1 class="headline">Herzlich willkommen bei Ihrer<br>Hausverwaltung im Raum Marburg</h1>

  <div class="features">
    <div class="feature">
      <svg viewBox="0 0 24 24"><path d="M3 11 12 3l9 8v10H3z"/></svg>
      <span>Fachliche<br>Erfahrung</span>
    </div>
    <div class="feature">
      <svg viewBox="0 0 24 24"><rect x="3" y="3" width="18" height="18"/><path d="M3 12h18M12 3v18"/></svg>
      <span>Professionelle<br>Beratung</span>
    </div>
    <div class="feature">
      <svg viewBox="0 0 24 24"><circle cx="12" cy="7" r="3"/><circle cx="5" cy="10" r="2"/><circle cx="19" cy="10" r="2"/><path d="M6 21v-5h12v5"/></svg>
      <span>Junges und<br>engagiertes Team</span>
    </div>
    <div class="feature">
      <svg viewBox="0 0 24 24"><path d="M3 7h18M5 7v12M9 7v12M15 7v12M19 7v12M3 20h18M4 4h16"/></svg>
      <span>Zukunftsfähig &amp;<br>Verantwortungsbewusst</span>
    </div>
  </div>
  <div class="features-rule"></div>

  <div class="offers-label">Unsere Angebote:</div>

  <section class="offer offer--special">
    <h2 class="offer-title"><span class="offer-num">1</span>Sondereigentumsverwaltung</h2>
    <ul class="offer-list">
      <li>Direkte Vertretung des Eigentümers gegenüber den Mietern</li>
      <li>Durchführung des gesamten Schriftverkehrs</li>
      <li>Vermietung über anerkannte Makler mit Bonitätsprüfung</li>
      <li>Ausarbeitung und Abschluss erprobter Mietverträge</li>
      <li>Durchführung der Wohnungsübergaben</li>
      <li>Überwachung der Miethöhe und Durchführung von Mietanpassungen</li>
      <li>Überwachung der Zahlungseingänge</li>
      <li>Durchführung des gesamten Zahlungsverkehr und Führen Ihres Mietkontos</li>
      <li>Erfassen der Ein- und Ausgaben</li>
      <li>Abrechnung aller Nebenkosten mit den Mietern</li>
      <li>Verwaltung der Mietkautionen</li>
      <li>Erstellung der jährlichen Gesamtabrechnung für den Eigentümer</li>
      <li>Veranlassen notwendiger Reparaturen und Erhaltungsmaßnahmen</li>
      <li>Einleitung von Sofortmaßnahmen in Notfällen.</li>
    </ul>
  </section>

  <section class="offer offer--owner">
    <h2 class="offer-title"><span class="offer-num">2</span>Wohneigentumsverwaltung</h2>
    <ul class="offer-list">
      <li>Verwaltung der gemeinschaftlichen Angelegenheiten</li>
      <li>Erstellung des Wirtschaftsplans</li>
      <li>Erstellung der Jahresberechnung</li>
      <li>Eigentümerversammlung und Niederschrift</li>
      <li>Verwaltung der gemeinschaftlichen Gelder</li>
      <li>Überwachen der Verträge der Gemeinschaft</li>
      <li>Zahlungsverkehr und Buchführung</li>
      <li>Auftragsvergabe gemäß Beschlussfassung</li>
      <li>Sofortmaßnahmen bei dringenden Schadensfällen</li>
      <li>Technische Betreuung des Gemeinschaftseigentums</li>
      <li>Sicherheitseinrichtungen</li>
      <li>Allgemeine Verwaltung mit Behörden und Eigentümern</li>
    </ul>
  </section>

  <section class="offer offer--rent">
    <h2 class="offer-title"><span class="offer-num">3</span>Mietverwaltung</h2>
    <ul class="offer-list">
      <li>Allgemeine Verwaltung</li>
      <li>Kaufmännische Verwaltung</li>
      <li>Technische Betreuung</li>
      <li>Nebenkostenabrechnungsservice</li>
    </ul>
  </section>

  <address class="contact" style="font-style:normal">
    <div class="contact-row">
      <svg viewBox="0 0 14 14"><path d="M1 7 7 1.5 13 7v6H1z"/></svg>
      <span>Lindenhofer Weg 12<br>35039 Marburg</span>
    </div>
    <div class="contact-row">
      <svg viewBox="0 0 14 14"><rect x="1" y="3" width="12" height="8"/><path d="M1 3l6 5 6-5"/></svg>
      <span>info@lwr-lahntal.de</span>
    </div>
    <div class="contact-row">
      <svg viewBox="0 0 14 14"><rect x="4" y="1" width="6" height="12" rx="1"/></svg>
      <span>06421 904512</span>
    </div>
  </address>

  <div class="web">www.<strong>LWR-LAHNTAL</strong>.de</div>
</div>
</body>
</html>
```